The Plate Compass

Cutting Through the Noise to What Actually Works.

Nutrition book

Target Market(s)

People looking to be or get healthy and eat right.

```html
<!DOCTYPE html>
<html lang="en">
<head>
<meta charset="utf-8">
<title>The Plate Compass — Book Cover</title>
<link rel="stylesheet" href="https://fonts.googleapis.com/css2?family=Playfair+Display:wght@500&family=Fredoka:wght@600&family=Didact+Gothic&family=Great+Vibes&display=swap">
<style>
  :root {
    --paper: #f8f5ec;
    --paper-shade: #efeadb;
    --ink-blue: #4a62ae;
    --ink-blue-deep: #3550a3;
    --text-dark: #2e2e2e;
    --white: #ffffff;
    --art-green: #6f8a4a;
    --art-red: #c9502e;
    --art-cream: #e8d9b4;
    --art-gold: #e2b74a;
  }
  html, body {
    margin: 0;
    padding: 0;
    width: 800px;
    height: 1200px;
    overflow: hidden;
    background: var(--paper);
  }
  p, h1 { margin: 0; }
  .cover {
    position: relative;
    width: 800px;
    height: 1200px;
    overflow: hidden;
    background:
      radial-gradient(ellipse at 50% 35%, var(--paper) 0%, var(--paper) 55%, var(--paper-shade) 100%);
  }
  .title-line {
    position: absolute;
    left: 0;
    width: 800px;
    text-align: center;
    font-family: "Playfair Display", serif;
    font-weight: 500;
    color: var(--ink-blue);
    line-height: 1;
  }
  .title-the { top: 30px; font-size: 114px; letter-spacing: 2px; }
  .title-plate { top: 140px; font-size: 114px; letter-spacing: 4px; }
  .title-band {
    position: absolute;
    left: 66px;
    top: 258px;
    width: 668px;
    height: 86px;
  }
  .title-band-word {
    position: absolute;
    left: 0;
    top: 258px;
    width: 800px;
    height: 86px;
    display: flex;
    align-items: center;
    justify-content: center;
    font-family: "Fredoka", sans-serif;
    font-weight: 600;
    font-size: 70px;
    line-height: 1;
    letter-spacing: 10px;
    text-indent: 10px;
    color: var(--white);
  }
  .subtitle {
    position: absolute;
    top: 380px;
    left: 0;
    width: 800px;
    text-align: center;
    font-family: "Didact Gothic", sans-serif;
    font-size: 26px;
    color: var(--text-dark);
  }
  .author {
    position: absolute;
    top: 446px;
    left: 0;
    width: 800px;
    text-align: center;
    font-family: "Great Vibes", cursive;
    font-size: 52px;
    line-height: 1.2;
    color: var(--ink-blue);
  }
  .plate-art {
    position: absolute;
    left: 82px;
    top: 530px;
    width: 668px;
    height: 490px;
    border-radius: 50%;
    background:
      radial-gradient(ellipse at 28% 40%, var(--art-red) 0%, rgba(201,80,46,0.6) 22%, transparent 45%),
      radial-gradient(ellipse at 22% 22%, var(--art-green) 0%, transparent 35%),
      radial-gradient(ellipse at 70% 30%, var(--art-cream) 0%, transparent 40%),
      radial-gradient(ellipse at 62% 72%, var(--art-gold) 0%, transparent 30%),
      radial-gradient(ellipse at 75% 70%, #efe9dc 0%, transparent 40%),
      radial-gradient(ellipse at 50% 50%, #b89a74 0%, #d9c9ad 60%, rgba(248,245,236,0) 72%);
  }
  .topics {
    position: absolute;
    left: 0;
    top: 1068px;
    width: 800px;
    height: 120px;
  }
  .topic {
    position: absolute;
    top: 0;
    width: 140px;
    margin-left: -70px;
    text-align: center;
  }
  .topic-badge {
    display: block;
    width: 96px;
    height: 76px;
    margin: 0 auto;
  }
  .topic-label {
    display: block;
    margin-top: 14px;
    font-family: "Didact Gothic", sans-serif;
    font-size: 14.5px;
    color: var(--text-dark);
    white-space: nowrap;
  }
</style>
</head>
<body>
<main class="cover">
  <h1 class="title-line title-the">THE</h1>
  <p class="title-line title-plate">PLATE</p>

  <svg class="title-band" viewBox="0 0 668 86" aria-hidden="true">
    <path fill="var(--ink-blue)" d="M6 14 L60 8 L180 12 L330 6 L480 10 L600 7 L662 14 L654 30 L666 44 L656 58 L664 74 L590 80 L440 76 L300 82 L160 77 L40 81 L4 74 L14 58 L2 44 L12 30 Z"/>
  </svg>
  <p class="title-band-word">COMPASS</p>

  <p class="subtitle">Cutting Through the Noise to What Actually Works.</p>
  <p class="author">By Mark Dalby</p>

  <div class="plate-art" role="img" aria-label="Sketched plate split into sections of vegetables, egg, tomatoes, potatoes, bread, asparagus and cheese"></div>

  <section class="topics">
    <div class="topic" style="left:128px">
      <svg class="topic-badge" viewBox="0 0 96 76" aria-hidden="true">
        <path fill="var(--ink-blue)" d="M10 14 Q48 2 86 10 Q96 38 88 64 Q48 76 8 66 Q0 38 10 14 Z"/>
        <g transform="rotate(-40 48 38)">
          <rect x="34" y="30" width="30" height="14" rx="7" fill="none" stroke="#fff" stroke-width="3"/>
          <rect x="49" y="30" width="15" height="14" rx="7" fill="#fff"/>
        </g>
        <circle cx="30" cy="26" r="2.5" fill="#fff"/><circle cx="38" cy="20" r="2" fill="#fff"/>
        <circle cx="62" cy="52" r="2.5" fill="#fff"/><circle cx="68" cy="44" r="2" fill="#fff"/>
      </svg>
      <span class="topic-label">Supplements</span>
    </div>
    <div class="topic" style="left:261px">
      <svg class="topic-badge" viewBox="0 0 96 76" aria-hidden="true">
        <path fill="var(--ink-blue)" d="M8 12 Q48 4 88 12 Q94 40 86 66 Q46 74 10 64 Q2 38 8 12 Z"/>
        <path fill="#fff" d="M34 30 H42 L52 22 V54 L42 46 H34 Z"/>
        <path d="M58 30 Q64 38 58 46 M62 26 Q72 38 62 50" fill="none" stroke="#fff" stroke-width="2.5"/>
        <line x1="30" y1="56" x2="64" y2="20" stroke="#fff" stroke-width="3"/>
      </svg>
      <span class="topic-label">Noise</span>
    </div>
    <div class="topic" style="left:391px">
      <svg class="topic-badge" viewBox="0 0 96 76" aria-hidden="true">
        <path fill="var(--ink-blue)" d="M10 10 Q50 4 86 12 Q94 40 88 64 Q48 74 8 66 Q2 36 10 10 Z"/>
        <path fill="#fff" d="M30 48 Q30 30 48 30 Q66 30 66 48 Z"/>
        <rect x="24" y="50" width="48" height="4" rx="2" fill="#fff"/>
        <path d="M40 24 Q37 20 40 16 M48 24 Q45 20 48 16 M56 24 Q53 20 56 16" fill="none" stroke="#fff" stroke-width="2"/>
      </svg>
      <span class="topic-label">Meal Timing</span>
    </div>
    <div class="topic" style="left:523px">
      <svg class="topic-badge" viewBox="0 0 96 76" aria-hidden="true">
        <path fill="var(--ink-blue)" d="M8 14 Q48 2 88 12 Q94 40 86 66 Q48 76 10 64 Q2 38 8 14 Z"/>
        <circle cx="48" cy="22" r="3" fill="#fff"/>
        <path fill="#fff" d="M30 40 Q30 24 48 24 Q66 24 66 40 Z"/>
        <rect x="26" y="41" width="44" height="4" rx="2" fill="#fff"/>
        <g fill="#fff">
          <polygon points="38,49 39.8,53 44,53 40.6,55.6 42,60 38,57 34,60 35.4,55.6 32,53 36.2,53"/>
          <polygon points="48,49 49.8,53 54,53 50.6,55.6 52,60 48,57 44,60 45.4,55.6 42,53 46.2,53"/>
          <polygon points="58,49 59.8,53 64,53 60.6,55.6 62,60 58,57 54,60 55.4,55.6 52,53 56.2,53"/>
        </g>
      </svg>
      <span class="topic-label">Food Quality</span>
    </div>
    <div class="topic" style="left:660px">
      <svg class="topic-badge" viewBox="0 0 96 76" aria-hidden="true">
        <path fill="var(--ink-blue)" d="M10 12 Q48 4 86 10 Q94 38 88 66 Q46 74 8 64 Q2 36 10 12 Z"/>
        <circle cx="40" cy="32" r="8" fill="#fff"/>
        <circle cx="54" cy="28" r="7" fill="#fff"/>
        <path fill="#fff" d="M26 40 H70 Q68 54 48 54 Q28 54 26 40 Z"/>
        <rect x="36" y="57" width="24" height="3" rx="1.5" fill="#fff"/>
      </svg>
      <span class="topic-label">Protein &amp; Calories</span>
    </div>
  </section>
</main>
</body>
</html>
```